Commercial Rooftop Solar business needs a website

We need a website with fantastic appeal for a new company based in Melbourne called Tallow Ridge Energy. We design and install solar energy systems for commercial applications across Australia. Our market is to focus on small to medium businesses looking for solar solutions, but we will also provide our service for residential customers. We would like a beautiful 'front page' feel to our home page, using photographs of solar PV systems and/or natural imagery. Our logo uses the colours orange and black, which could easily be echoed in photographic imagery of sunset and sunrise, for example. The design should communicate quiet confidence and professionalism to a corporate marketplace.

NEW POINTS FOR BRIEF: This design also needs to be flexible to allow for additional future content, including a Support page with sub pages, FAQ's, and a Blog.

As part of this design project, we will require the coding for the website to be completed by the designer.

We have seen some websites, which we like the look and feel of: these are listed below.

brightvanepower.com.au:

• Beautiful images underlaying brief text selling points.
• Simple ‘front cover’ style home page with elegant drop-down menu, stylish simple font style.
• Home page invites exploration through the menu links, rather than trying to provide all the information up front.
• Company logo and name in the top left hand corner, contact details accessible at top right hand, seems consistent in most sites.

kelpworks.com.au

rumbofield.com:
• Same element as the others is the front-page style home page with beautiful images underlying text.

We have a webpage that we started uploading content to. You can use some of the content there in your designs: www.tallowridgeenergy.com.au

Technical Specifications:
PAGES:

Home

About Us

Solutions - Commercial
- Residential

Products - Solar Panels - Vorla Heron, Vorla TELD, Vorla QB
- Solar Inverters - Kestamo, BrilQuill
- Monitoring systems - Dunmere Metrics
- Batteries - RW

- Datasheets have been provided for reference but if it's too much work, you can use generic text and we will provide content later.

Contact Us

FUTURE PAGES (Please consider in structure, where links could be placed):

Support

FAQ's

Blog.

We could provide some content for the Support page soon, but the Blog and FAQ's are future pages which we don't want highlighted in the design as we don't yet have content.

Phone: 1800 7 BIRCH
Email: sales@tallowridgeenergy.com.au

Currently, I do not have images and text available. Please
use placeholders in the meantime. The final text and images will be uploaded for the winner once a winning design has been selected.

Target Market(s)

Primary focus is on small to medium sized business owners. Those owners will have a house which may be suitable for solar so we want to cater to residential deeper in the website.

Industry/Entity Type

Solar Energy

Coding

Coded - Design and coding required

Number of Pages Required

5+ page

Colors
f78f20
0255a3

Requirements
Must have
• Logo as per attachments.
Nice to have
• Logo can have alternate colours Eg. White on Orange or Black etc. provided colour correct logo is shown somewhere eg. footer or contact page.
• In the active site, I'd like to have:
• Very slowly zooming images - barely perceptible.
• Title text that rolls into place
• Subtle movements
• See https://plumtally.com.au/ for example

```html
<!DOCTYPE html>
<html lang="en">
<head>
<meta charset="utf-8">
<title>Tallow Ridge Energy – Solar PV Systems</title>
<link rel="stylesheet" href="https://fonts.googleapis.com/css2?family=Raleway:wght@500;600;700;800&family=Open+Sans:wght@400;600&display=swap">
<style>
:root{
  --orange:#ee5a26;
  --orange-soft:#f07a3e;
  --charcoal:#3b3b3b;
  --ink:#2b2b2b;
  --footer:#1d1d1d;
  --text:#555;
  --white:#fff;
  --heading:"Raleway",sans-serif;
  --body:"Open Sans",sans-serif;
}
*{box-sizing:border-box;margin:0;padding:0}
html,body{width:1200px;height:2899px;overflow:hidden}
body{position:relative;background:var(--white);font-family:var(--body);color:var(--text)}
.abs{position:absolute}

/* hero */
.hero{left:0;top:0;width:1200px;height:634px;background:linear-gradient(120deg,#3d5a3a 0%,#5d7a3f 22%,#2a3d5c 48%,#1b2a4a 75%,#0f1a33 100%)}
.hero-shade{left:0;top:0;width:1200px;height:634px;background:rgba(10,15,30,.25)}
.brand{left:100px;top:70px;font-family:var(--heading);font-weight:700;font-size:28px;color:var(--white);display:flex;align-items:center;gap:12px}
.brand .dot{width:22px;height:22px;border-radius:50%;background:var(--orange)}
.topbar{right:101px;top:35px;display:flex;align-items:center;gap:14px;font-family:var(--heading);font-weight:700;font-size:16px;color:var(--white)}
.quick{background:var(--orange);border-radius:18px;padding:8px 18px;font-size:13px}
.nav{right:101px;top:88px;display:flex;gap:34px;font-family:var(--heading);font-weight:600;font-size:18px;color:var(--white)}
.hero-title{left:0;width:1200px;top:256px;text-align:center;font-family:var(--heading);font-weight:800;font-size:54px;color:var(--white)}
.hero-sub{left:350px;width:500px;top:330px;text-align:center;font-family:var(--heading);font-weight:700;font-size:17px;line-height:23px;color:var(--white)}
.btn-ghost{left:547px;top:400px;width:106px;height:32px;border:1px solid var(--white);color:var(--white);font-family:var(--heading);font-weight:700;font-size:12px;display:flex;align-items:center;justify-content:center}
.arrow{top:355px;color:rgba(255,255,255,.7);font-size:24px}

/* solution tiles */
.tile{top:560px;width:500px;height:184px;color:var(--white);padding:35px 30px 0 115px}
.tile.commercial{left:99px;background:var(--charcoal)}
.tile.residential{left:599px;background:var(--orange)}
.tile h3{font-family:var(--heading);font-weight:700;font-size:22px;margin-bottom:8px}
.tile p{font-size:11.5px;line-height:20px}
.tile svg.icon{position:absolute;left:18px;top:40px}
.tile .corner{position:absolute;right:14px;bottom:8px;font-size:11px;opacity:.7}
.tile-shadow{left:130px;top:744px;width:940px;height:40px;background:radial-gradient(ellipse at top,rgba(0,0,0,.18),transparent 70%)}

/* welcome */
.welcome-mark{left:566px;top:820px;width:68px;height:68px;border-radius:50%;background:var(--orange)}
.welcome-title{left:0;width:1200px;top:896px;text-align:center;font-family:var(--heading);font-weight:700;font-size:46px;color:var(--ink)}
.welcome-title span{color:var(--orange)}
.welcome-text{left:168px;width:864px;top:962px;text-align:center;font-size:11.5px;line-height:21px;color:var(--text)}
.btn-solid{background:var(--orange);color:var(--white);border-radius:16px;font-family:var(--heading);font-weight:700;font-size:11px;display:flex;align-items:center;justify-content:center}
.welcome-btn{left:549px;top:1070px;width:104px;height:31px}

/* how it works */
.how{left:0;top:1120px;width:1200px;height:547px}
.how-title{left:0;width:1200px;top:1266px;text-align:center;font-family:var(--heading);font-weight:700;font-size:30px;color:var(--white)}
.step{top:1340px;width:210px;text-align:center;color:var(--white);font-size:13.5px;line-height:21px}
.step svg{display:block;margin:0 auto 10px}

/* systems */
.sys-title{left:0;width:1200px;top:1716px;text-align:center;font-family:var(--heading);font-weight:700;font-size:33px;color:var(--ink)}
.sys-text{left:230px;width:740px;top:1772px;text-align:center;font-size:11.5px;line-height:21px}
.card{top:1860px;width:316px}
.card .photo{width:316px;height:183px;border:4px solid #eee}
.card h4{font-family:var(--heading);font-weight:600;font-size:17px;color:var(--ink);margin:24px 0 10px}
.card p{font-size:11.5px;line-height:21px}

/* newsletter */
.news{left:0;top:2231px;width:1200px;height:300px;background:linear-gradient(90deg,#e6541f,#ef6a2e 50%,#e8774a)}
.news-title{left:0;width:1200px;top:2292px;text-align:center;font-family:var(--heading);font-weight:700;font-size:37px;color:var(--white)}
.news-text{left:280px;width:640px;top:2356px;text-align:center;font-size:13px;line-height:22px;color:var(--white)}
.news-input{left:280px;top:2419px;width:472px;height:42px;background:var(--white);border-radius:2px;padding:12px 16px;font-size:13px;color:#888}
.news-btn{left:765px;top:2419px;width:155px;height:42px;background:var(--ink);color:var(--white);font-family:var(--heading);font-weight:700;font-size:14px;display:flex;align-items:center;justify-content:center}

/* footer */
.footer{left:0;top:2531px;width:1200px;height:368px;background:var(--footer)}
.foot-brand{left:97px;top:2640px;width:170px;font-family:var(--heading);font-weight:700;font-size:22px;line-height:28px;color:var(--white)}
.foot-col h5{font-family:var(--heading);font-weight:700;font-size:18px;color:var(--white);margin-bottom:20px}
.foot-col{top:2585px;color:#ddd;font-size:12.5px;line-height:21px}
.contact-row{display:flex;gap:14px;margin-bottom:16px}
.contact-row svg{flex:none;margin-top:2px}
.foot-input{width:284px;height:40px;background:var(--white);color:#777;padding:11px 14px;font-size:12px;margin:14px 0 14px}
.foot-sub{width:112px;height:38px;background:var(--orange);color:var(--white);font-family:var(--heading);font-weight:700;font-size:13px;display:flex;align-items:center;justify-content:center}
.copyright{left:0;width:1200px;top:2850px;text-align:center;font-size:12px;color:#ccc}
</style>
</head>
<body>

<div class="abs hero" role="img" aria-label="Photograph of solar panels in a green field under a blue sky"></div>
<div class="abs hero-shade"></div>
<div class="abs brand"><span class="dot"></span>Tallow Ridge Energy</div>
<div class="abs topbar">
  <svg width="18" height="18" viewBox="0 0 24 24" fill="#fff"><path d="M6.6 10.8a15 15 0 0 0 6.6 6.6l2.2-2.2a1 1 0 0 1 1-.25 11.4 11.4 0 0 0 3.6.57 1 1 0 0 1 1 1V20a1 1 0 0 1-1 1A17 17 0 0 1 3 4a1 1 0 0 1 1-1h3.5a1 1 0 0 1 1 1c0 1.25.2 2.45.57 3.6a1 1 0 0 1-.25 1z"/></svg>
  <span>Phone : 908 5521 0416</span>
  <span class="quick">QUICK CONTACT</span>
</div>
<nav class="abs nav"><span>Home</span><span>About Us</span><span>Our Solutions ▾</span><span>Contact Us</span></nav>
<h1 class="abs hero-title">SOLAR PV SYSTEMS</h1>
<p class="abs hero-sub">We design and install solar energy systems for commercial applications across Australia</p>
<div class="abs btn-ghost">READ MORE</div>
<div class="abs arrow" style="left:44px">‹</div>
<div class="abs arrow" style="left:1140px">›</div>

<div class="abs tile-shadow"></div>
<div class="abs tile commercial">
  <svg class="icon" width="80" height="70" viewBox="0 0 80 70" fill="none" stroke="#fff" stroke-width="2.5"><path d="M12 10h56l-8 38H4z"/><path d="M26 10l-6 38M40 10l-4 38M54 10l-2 38M9 23h57M6 36h58"/><path d="M34 48v12M22 62h28"/></svg>
  <h3>COMMERCIAL</h3>
  <p>Lorem ipsum dolor sit amet, consectetur adipiscing elit, sed do eiusmod tempor incididunt ut labore et dolore magna aliqua. Ut enim ad minim veniam, quis nostrud exercitation ullamco laboris nisi ut aliquip</p>
  <span class="corner">↘</span>
</div>
<div class="abs tile residential">
  <svg class="icon" width="76" height="76" viewBox="0 0 76 76" fill="none" stroke="#fff" stroke-width="2.5"><path d="M8 36L38 8l30 28M16 30v38h44V30"/><circle cx="38" cy="46" r="7"/><path d="M38 33v-4M38 63v-4M25 46h-4M55 46h-4M29 37l-3-3M50 58l-3-3M47 37l3-3M26 58l3-3"/></svg>
  <h3>RESIDENTIAL</h3>
  <p>Lorem ipsum dolor sit amet, consectetur adipiscing elit, sed do eiusmod tempor incididunt ut labore et dolore magna aliqua. Ut enim ad minim veniam, quis nostrud exercitation ullamco laboris nisi ut aliquip</p>
  <span class="corner">↘</span>
</div>

<div class="abs welcome-mark"></div>
<h2 class="abs welcome-title">Welcome To <span>Tallow Ridge Energy</span></h2>
<p class="abs welcome-text">Sed ut perspiciatis unde omnis iste natus error sit voluptatem accusantium doloremque laudantium, totam rem aperiam, eaque ipsa quae ab illo inventore veritatis et quasi architecto beatae vitae dicta sunt explicabo. Nemo enim ipsam voluptatem quia voluptas sit aspernatur aut odit aut fugit, sed quia consequuntur magni dolores eos qui ratione voluptatem sequi nesciunt. Neque porro quisquam est, qui dolorem ipsum quia dolor sit amet, consectetur, adipisci velit, sed quia non numquam eius modi tempora incidunt ut labore et dolore magnam aliquam quaerat voluptatem. Ut enim ad minima veniam, quis nostrum</p>
<div class="abs btn-solid welcome-btn">READ MORE ➜</div>

<svg class="abs how" viewBox="0 0 1200 547" role="img" aria-label="Dusk photograph of a large solar farm under a dark sky">
  <defs><linearGradient id="howBg" x1="0" y1="0" x2="0" y2="1"><stop offset="0" stop-color="#3a3d45"/><stop offset=".45" stop-color="#2a2f3a"/><stop offset="1" stop-color="#1c2230"/></linearGradient></defs>
  <polygon points="0,0 1200,116 1200,426 0,547" fill="url(#howBg)"/>
</svg>
<h2 class="abs how-title">HOW IT WORKS</h2>
<svg class="abs" style="left:0;top:1355px" width="1200" height="60" fill="none" stroke="#fff" stroke-width="2" stroke-dasharray="5 4">
  <path d="M293 40 q40-14 72-6"/><path d="M572 40 q40 10 72 -2"/><path d="M832 40 q40-14 72-6"/>
  <path d="M360 30l6 4-6 4M639 34l6 4-6 4M899 30l6 4-6 4" stroke-dasharray="none"/>
</svg>
<div class="abs step" style="left:82px">
  <svg width="96" height="110" viewBox="0 0 96 110" fill="none" stroke="#fff" stroke-width="2.5"><path d="M48 104l-12-14a44 44 0 1 1 24 0z" fill="rgba(255,255,255,.05)"/><circle cx="48" cy="38" r="8" fill="#fff"/><path d="M32 62a16 14 0 0 1 32 0z" fill="#fff"/></svg>
  Tallow Ridge Energy checks that every person gets a solar system that pays for itself in energy savings from day one
</div>
<div class="abs step" style="left:359px">
  <svg width="96" height="110" viewBox="0 0 96 110" fill="none" stroke="#fff" stroke-width="2.5"><path d="M48 104l-12-14a44 44 0 1 1 24 0z" fill="rgba(255,255,255,.05)"/><circle cx="48" cy="46" r="16"/><circle cx="48" cy="46" r="8"/><circle cx="48" cy="46" r="2" fill="#fff"/></svg>
  Tallow Ridge Energy organises for the solar system to be installed
</div>
<div class="abs step" style="left:631px">
  <svg width="96" height="110" viewBox="0 0 96 110" fill="none" stroke="#fff" stroke-width="2.5"><path d="M48 104l-12-14a44 44 0 1 1 24 0z" fill="rgba(255,255,255,.05)"/><path d="M30 34h36l-4 20H26z"/><path d="M40 34l-2 20M52 34l-1 20M28 44h36M46 54v8M38 62h16"/></svg>
  Tallow Ridge Energy supports pensioners to understand and get the most out of solar
</div>
<div class="abs step" style="left:909px">
  <svg width="96" height="110" viewBox="0 0 96 110" fill="none" stroke="#fff" stroke-width="2.5"><path d="M48 104l-12-14a44 44 0 1 1 24 0z" fill="rgba(255,255,255,.05)"/><rect x="28" y="34" width="40" height="24"/><circle cx="48" cy="46" r="7" fill="#fff"/></svg>
  Pensioners gradually pay for cost through their usual rates payments at 0% interest
</div>

<h2 class="abs sys-title">SOLAR ENERGY SYSTEMS</h2>
<p class="abs sys-text">Sed ut perspiciatis unde omnis iste natus error sit voluptatem accusantium doloremque laudantium, totam rem aperiam, eaque ipsa quae ab illo inventore veritatis et quasi architecto beatae vitae dicta sunt explicabo.</p>
<div class="abs card" style="left:99px">
  <div class="photo" role="img" aria-label="Illustration of solar panels arranged on a yellow grid structure" style="background:linear-gradient(135deg,#e8a21a,#c97d12 50%,#4a5fa8)"></div>
  <h4>Coordinating Household Promotion</h4>
  <p>Lorem ipsum dolor sit amet, consectetur adipiscing elit, sed do eiusmod tempor incididunt ut labore et dolore magna aliqua. Ut enim ad minim veniam,</p>
</div>
<div class="abs card" style="left:442px">
  <div class="photo" role="img" aria-label="Photograph of a worker installing rooftop solar panels under a blue sky" style="background:linear-gradient(180deg,#4f86c8,#a9c6e4 45%,#2c3b57)"></div>
  <h4>Administering The Installations</h4>
  <p>Lorem ipsum dolor sit amet, consectetur adipiscing elit, sed do eiusmod tempor incididunt ut labore et dolore magna aliqua. Ut enim ad minim veniam,</p>
</div>
<div class="abs card" style="left:783px">
  <div class="photo" role="img" aria-label="Photograph of an engineer in a hard hat reviewing a solar array" style="background:linear-gradient(135deg,#e2e8ef,#8fb0d4 50%,#3f6fa8)"></div>
  <h4>Evaluating The Project</h4>
  <p>Lorem ipsum dolor sit amet, consectetur adipiscing elit, sed do eiusmod tempor incididunt ut labore et dolore magna aliqua. Ut enim ad minim veniam,</p>
</div>

<div class="abs news" role="img" aria-label="Orange-toned photograph of solar panels with a city skyline"></div>
<h2 class="abs news-title">JOIN THE NEWSLETTER</h2>
<p class="abs news-text">Sed ut perspiciatis unde omnis iste natus error sit voluptatem accusantium doloremque laudantium, totam rem aperiam, eaque ipsa quae ab illo inventore veritatis et quasi</p>
<div class="abs news-input">email</div>
<div class="abs news-btn">JOIN NOW!</div>

<footer>
  <div class="abs footer"></div>
  <div class="abs foot-brand">Tallow Ridge Energy</div>
  <div class="abs foot-col" style="left:309px;width:260px">
    <h5>CONTACT US</h5>
    <div class="contact-row">
      <svg width="16" height="20" viewBox="0 0 16 20" fill="none" stroke="#fff" stroke-width="1.6"><path d="M8 19s6-6.5 6-11A6 6 0 0 0 2 8c0 4.5 6 11 6 11z"/><circle cx="8" cy="8" r="2"/></svg>
      <span>Tallow Ridge Energy<br>Harrow Lane, Fenbury, Wexmoor.</span>
    </div>
    <div class="contact-row">
      <svg width="16" height="16" viewBox="0 0 24 24" fill="none" stroke="#fff" stroke-width="2"><path d="M6.6 10.8a15 15 0 0 0 6.6 6.6l2.2-2.2 4.6 1V20A17 17 0 0 1 3 4h4.2l1 4.6z"/></svg>
      <span>Phone : +44(0)20 5550 1187</span>
    </div>
    <div class="contact-row">
      <svg width="16" height="14" viewBox="0 0 16 14" fill="none" stroke="#fff" stroke-width="1.6"><rect x="1" y="1" width="14" height="12"/><path d="M1 1l7 6 7-6"/></svg>
      <span>admin@tallowridgeenergy.com</span>
    </div>
  </div>
  <div class="abs foot-col" style="left:622px;width:290px">
    <h5>SIGN UP TO RECEIVE EMAIL</h5>
    <p style="font-size:11.5px;line-height:19px">Excepteur sint occaecat cupidatat non proident, sunt in culpa qui Nemo enim ipsam voluptatem</p>
    <div class="foot-input">Enter Name</div>
    <div class="foot-sub">SUBSCRIBE</div>
  </div>
  <div class="abs foot-col" style="left:983px;width:140px">
    <h5>QUICK LINKS</h5>
    <div>Home</div><div>About Us</div><div>Solutions</div><div>Contact Us</div>
  </div>
  <p class="abs copyright">Copyright © Tallow Ridge Energy 2017. All rights reserved.</p>
</footer>

</body>
</html>
```